Steel Rebar Fabrication Company needs Facebook Ads & page, Instagram Ads & pages designed.

I want to put out an Instagram, Facebook ad, and LinkedIn campaign out for my new company, Ridgeline Metals Inc. I want the ads to be short but clean, clear and precise. I want our address: 4871 Marrowfield Rd. Tsawwassen, BC. I want our hours of operation to be listed 8:00am to 4:00pm Monday to Friday. Product Delivery to your job site or pick up at our yard available. We can cut, bend to custom and standard shapes based upon Canadian CSA Standards. We offer products ranging from 10mm to 35mm diameter Grade 400W rebar. We can bend stirrups, dowels, hairpins; whatever your company needs to complete your product. Whether it is a small project, Tilt Up warehouse, Wood Frame Construction with Concrete parkade foundation; we have the team to meet your needs.
Email address: info@ridgelinemetalsinc.ca
We can service all areas of British Columbia.

Target Market(s)

Construction Company's for homes, condominiums, warehouses, commercial, industrial, and infrastructure projects. As well, as the every day DIY home improvement or renovator.

Industry/Entity Type

Construction

Requirements
Nice to have
• Would like to see a image of the rebar steel that I have provided in the ad. Even if it is in the background with a lower opacity level. Bonus if someone includes any of the movie files I have uploaded.

```html
<!DOCTYPE html>
<html lang="en">
<head>
<meta charset="utf-8">
<title>Ridgeline Metals Inc. — Rebar Fabrication</title>
<link href="https://fonts.googleapis.com/css2?family=Montserrat:wght@300;400;500;700;800&display=swap" rel="stylesheet">
<style>
  :root{
    --red:#c01f2f;
    --ink:#1f1f1f;
    --white:#ffffff;
  }
  *{box-sizing:border-box;margin:0;padding:0}
  html,body{width:1200px;height:1200px;overflow:hidden;background:var(--white)}
  body{font-family:'Montserrat',sans-serif;color:var(--ink)}
  .ad{position:relative;width:1200px;height:1200px;background:var(--white);overflow:hidden}
  .abs{position:absolute}

  .brand{left:44px;top:40px;font-weight:800;font-size:46px;line-height:1.02;color:var(--ink);letter-spacing:1px}

  .kicker{left:44px;top:194px;font-weight:400;font-size:22px;letter-spacing:9.5px;color:var(--red)}
  .headline{left:40px;top:226px;font-weight:800;font-size:62px;line-height:58px;color:var(--red);letter-spacing:-.5px}

  .hours-band{left:0;top:365px;width:500px;height:119px}
  .hours-label{left:28px;top:377px;width:350px;height:35px;background:var(--white);border-radius:3px;
    color:var(--red);font-weight:700;font-size:27px;line-height:35px;padding-left:16px}
  .hours-time{left:44px;top:414px;color:var(--white);font-weight:700;font-size:30px}
  .hours-time .to{font-weight:400}
  .hours-days{left:44px;top:449px;color:var(--white);font-weight:300;font-size:27px}

  .services{left:28px;top:507px;width:457px;height:394px;background:var(--ink);border-radius:24px 24px 0 0}
  .services-title{left:38px;top:516px;width:432px;height:47px;background:var(--red);border-radius:14px 14px 0 0;
    color:var(--white);font-weight:700;font-size:27px;line-height:47px;padding-left:56px}
  .service-list{left:44px;top:578px;width:440px;list-style:none}
  .service-list li{position:relative;padding-left:31px;color:var(--white);font-weight:400;font-size:16px;line-height:21px;margin-bottom:22px;letter-spacing:.2px;white-space:nowrap}
  .service-list li svg{position:absolute;left:0;top:3px}

  .delivery{left:28px;top:912px;width:457px;height:153px;background:var(--red);border-radius:0 0 24px 24px;
    display:flex;align-items:center;justify-content:center;text-align:center;
    color:var(--white);font-weight:700;font-size:26px;line-height:30px}

  .email{left:44px;top:1103px;display:flex;align-items:center;gap:14px;font-size:21px;font-weight:400;white-space:nowrap}
  .divider{left:458px;top:1086px;width:2px;height:64px;background:var(--ink)}
  .address{left:504px;top:1088px;display:flex;align-items:flex-start;gap:14px}
  .address svg{margin-top:12px}
  .address p{font-size:30px;line-height:44px;font-weight:400;white-space:nowrap}

  .stripe{left:882px;top:0;width:16px;height:1200px;background:var(--red)}
  .rebar-bg{left:898px;top:0;width:302px;height:1200px;
    background:linear-gradient(180deg,#8e8e8e 0%,#b7b7b7 22%,#6d6d6d 45%,#9a9a9a 70%,#5c5c5c 100%)}
  .frame{left:898px;top:61px;width:266px;height:1078px;border:2px solid var(--white);border-left:none}

  .photo{border-radius:10px}
  .photo-main{left:525px;top:116px;width:598px;height:651px;
    background:linear-gradient(135deg,#cfd3d0 0%,#8a6b52 40%,#6e5644 60%,#b9c9d3 85%,#8fa6b0 100%)}
  .photo-small-a{left:525px;top:787px;width:290px;height:161px;
    background:linear-gradient(160deg,#8b6a4b 0%,#d99aa0 55%,#e6aab0 100%)}
  .photo-small-b{left:833px;top:787px;width:290px;height:161px;
    background:linear-gradient(160deg,#c9a77d 0%,#3a3a3a 40%,#8a5f8e 100%)}

  .service-area{left:525px;top:978px;width:343px;height:76px;background:var(--ink);border-radius:8px;
    color:var(--white);text-align:center;font-weight:400;font-size:19.5px;line-height:24px;padding-top:14px;letter-spacing:.3px}
  .service-area strong{color:var(--red);font-weight:700}
</style>
</head>
<body>
<main class="ad">
  <div class="abs rebar-bg" role="img" aria-label="Grayscale close-up of tied rebar mesh over formwork"></div>
  <div class="abs frame"></div>
  <div class="abs stripe"></div>

  <h1 class="abs brand">RIDGELINE<br>METALS INC.</h1>

  <p class="abs kicker">YOUR CHANCE NOW</p>
  <h2 class="abs headline">BUILD YOUR<br>DREAM</h2>

  <svg class="abs hours-band" viewBox="0 0 500 119" aria-hidden="true">
    <polygon points="0,0 418,0 500,119 0,119" fill="var(--red)"/>
  </svg>
  <div class="abs hours-label">OPERATION HOURS</div>
  <p class="abs hours-time">8:00AM <span class="to">TO</span> 4:00PM</p>
  <p class="abs hours-days">MONDAY TO FRIDAY</p>

  <section class="abs services"></section>
  <h3 class="abs services-title">OUR SERVICES</h3>
  <ul class="abs service-list">
    <li><svg width="15" height="14" viewBox="0 0 15 14"><rect x="1" y="2" width="11" height="11" fill="none" stroke="var(--red)" stroke-width="1.8"/><path d="M4 7l3 3 7-8" fill="none" stroke="var(--red)" stroke-width="2"/></svg>We can cut, bend to custom and standard<br>shapes based upon Canadian CSA Standards</li>
    <li><svg width="15" height="14" viewBox="0 0 15 14"><rect x="1" y="2" width="11" height="11" fill="none" stroke="var(--red)" stroke-width="1.8"/><path d="M4 7l3 3 7-8" fill="none" stroke="var(--red)" stroke-width="2"/></svg>We can bend stirrups, dowels, hairpins;<br>whatever your company needs to complete<br>your product.</li>
    <li><svg width="15" height="14" viewBox="0 0 15 14"><rect x="1" y="2" width="11" height="11" fill="none" stroke="var(--red)" stroke-width="1.8"/><path d="M4 7l3 3 7-8" fill="none" stroke="var(--red)" stroke-width="2"/></svg>We offer products ranging from 10mm to<br>35mm diameter Grade400W rebar.</li>
    <li><svg width="15" height="14" viewBox="0 0 15 14"><rect x="1" y="2" width="11" height="11" fill="none" stroke="var(--red)" stroke-width="1.8"/><path d="M4 7l3 3 7-8" fill="none" stroke="var(--red)" stroke-width="2"/></svg>Whether it is a small project, Tilt Up<br>warehouse, Wood Frame Construction with<br>Concrete parkade foundation; we have the<br>team to meet your needs.</li>
  </ul>

  <div class="abs delivery">PRODUCT DELIVERY TO<br>YOUR JOB SITE OR PICK UP<br>AT OUR YARD AVAILABLE</div>

  <div class="abs email">
    <svg width="32" height="24" viewBox="0 0 34 26" aria-hidden="true"><rect width="34" height="26" rx="2" fill="var(--red)"/><path d="M2 3l15 11L32 3" fill="none" stroke="var(--white)" stroke-width="2.5"/></svg>
    <span>info@ridgelinemetalsinc.ca</span>
  </div>
  <div class="abs divider"></div>
  <div class="abs address">
    <svg width="38" height="46" viewBox="0 0 38 46" aria-hidden="true">
      <ellipse cx="19" cy="40" rx="18" ry="5" fill="var(--red)"/>
      <path d="M19 2c-8 0-13 6-13 13 0 9 13 25 13 25s13-16 13-25c0-7-5-13-13-13z" fill="var(--red)" stroke="var(--white)" stroke-width="2"/>
      <circle cx="19" cy="15" r="5" fill="var(--white)"/>
    </svg>
    <p>4871 Marrowfield<br>Rd. Tsawwassen, BC.</p>
  </div>

  <div class="abs photo photo-main" role="img" aria-label="Aerial drone view of a riverside construction site with a rebar-covered foundation slab"></div>
  <div class="abs photo photo-small-a" role="img" aria-label="Rebar grid laid over pink insulation inside formwork"></div>
  <div class="abs photo photo-small-b" role="img" aria-label="Close view of tied rebar mesh above purple insulation boards"></div>

  <div class="abs service-area">WE CAN SERVICE ALL AREAS<br>OF <strong>BRITISH COLUMBIA</strong></div>
</main>
</body>
</html>
```